Velvet Dice Night Age Verification Landing Page

To create a visually appealing design for the landing page of the adult game "Velvet Dice Night" that confirms the visitor's age.
The design should have a simple and visually appealing look that focuses on two buttons labeled "Yes" and "No". The purpose of the page is to confirm that the visitor is 18 years of age or older before accessing the game's content. Responsive design that works well on desktop and mobile devices. The final output should be delivered in PSD, AI, or Sketch format, along with any necessary images or assets.
I have also attached examples.

```html
<!DOCTYPE html>
<html lang="en">
<head>
<meta charset="utf-8">
<title>Velvet Dice Night – Age Verification</title>
<link href="https://fonts.googleapis.com/css2?family=Poppins:wght@400;500;600&display=swap" rel="stylesheet">
<style>
  :root {
    --scene-dark: #0b0a0b;
    --scene-mid: #2a2426;
    --scene-warm: #3b3133;
    --panel-bg: rgba(10, 9, 10, 0.55);
    --text-light: #ffffff;
    --brand-purple: #a25dae;
    --brand-lilac: #b98bc6;
    --button-light: #ffffff;
    --button-dark-text: #1c1a1c;
  }
  * { box-sizing: border-box; margin: 0; padding: 0; }
  html, body {
    width: 1200px;
    height: 600px;
    overflow: hidden;
    background: var(--scene-dark);
    font-family: "Poppins", sans-serif;
  }
  .age-gate {
    position: relative;
    width: 1200px;
    height: 600px;
    overflow: hidden;
  }
  .backdrop {
    position: absolute;
    inset: 0;
    background:
      radial-gradient(ellipse 30% 55% at 50% 45%, var(--scene-warm) 0%, rgba(59,49,51,0) 70%),
      radial-gradient(ellipse 25% 40% at 88% 30%, #4a4a48 0%, rgba(74,74,72,0) 70%),
      linear-gradient(180deg, #1b1718 0%, var(--scene-mid) 55%, #1a1718 100%);
  }
  .verify-panel {
    position: absolute;
    left: 334px;
    top: 143px;
    width: 532px;
    height: 313px;
    background: var(--panel-bg);
    border-radius: 3px;
    display: flex;
    flex-direction: column;
    align-items: center;
  }
  .brand-name {
    margin-top: 56px;
    display: flex;
    align-items: center;
    gap: 8px;
    font-size: 20px;
    font-weight: 500;
    color: var(--brand-lilac);
    line-height: 1;
  }
  .brand-dot {
    width: 12px;
    height: 12px;
    border-radius: 50%;
    background: var(--brand-lilac);
  }
  .question {
    margin-top: 38px;
    font-size: 31px;
    font-weight: 500;
    color: var(--text-light);
    line-height: 1;
    letter-spacing: -0.2px;
  }
  .choices {
    margin-top: 22px;
    display: flex;
    gap: 9px;
  }
  .choice {
    width: 98px;
    height: 43px;
    border: none;
    border-radius: 22px;
    font-family: "Poppins", sans-serif;
    font-size: 17px;
    font-weight: 600;
    cursor: pointer;
  }
  .choice--yes { background: var(--brand-purple); color: var(--text-light); }
  .choice--no { background: var(--button-light); color: var(--button-dark-text); }
  .remember {
    margin-top: 23px;
    display: flex;
    align-items: center;
    gap: 9px;
    font-size: 16px;
    color: var(--text-light);
  }
  .remember-box {
    width: 12px;
    height: 12px;
    border: 1.5px solid var(--text-light);
    border-radius: 2px;
  }
</style>
</head>
<body>
  <main class="age-gate">
    <div class="backdrop" role="img" aria-label="Dimly lit loft bedroom photo with a couple embracing on a bed, brick walls and potted plants"></div>
    <section class="verify-panel">
      <div class="brand-name"><span class="brand-dot"></span>Velvet Dice Night</div>
      <h1 class="question">Are you over 18 years of age?</h1>
      <div class="choices">
        <button class="choice choice--yes">YES</button>
        <button class="choice choice--no">NO</button>
      </div>
      <label class="remember"><span class="remember-box"></span>Remember me</label>
    </section>
  </main>
</body>
</html>
```